Business Card for Professional Photographer

I'm looking for an eye catching modern clean design that compliments my logo/ website fonts & colours.
I specialise in architecture, corporate & commercial photography so I'm marketing to professional clients rather than portrait / wedding clients.

I would prefer to not have a solid black design.

My logo brand guide is as follows :

Main front font. : Reislust
Main font colour : #fff
Slogan front font : Ubuntu Bold
Monogram front font : Venti Medium
Container colour : #fff

I need print ready files in pdf .png & .eps formats.

Included in the files below are some screen grabs as reference to font & colours etc.

```html
<!DOCTYPE html>
<html lang="en">
<head>
<meta charset="utf-8">
<title>Clearline Studio – Business Card</title>
<link rel="stylesheet" href="https://fonts.googleapis.com/css2?family=Ubuntu:wght@300;400;500&display=swap">
<style>
  :root {
    --page-bg: #ecebe8;
    --card-white: #ffffff;
    --gold: #c9974a;
    --gold-deep: #d2a05c;
    --gold-light: #fbf0b6;
    --ink: #3a3a3a;
    --ink-soft: #555555;
    --rule: #8f8f8f;
    --emboss: #3b3b3b;
  }
  * { box-sizing: border-box; margin: 0; padding: 0; }
  html, body { width: 1200px; height: 716px; overflow: hidden; }
  body {
    background: var(--page-bg);
    font-family: "Ubuntu", sans-serif;
    position: relative;
  }
  .card {
    position: absolute;
    top: 204px;
    width: 540px;
    height: 308px;
    box-shadow: 0 6px 18px rgba(0,0,0,0.18);
    overflow: hidden;
  }
  /* Front */
  .card-front { left: 40px; background: var(--card-white); }
  .brand {
    position: absolute;
    top: 62px;
    right: 48px;
    display: flex;
    align-items: center;
    gap: 12px;
  }
  .brand-mark {
    width: 34px; height: 34px;
    border: 2px solid var(--gold);
    border-radius: 50%;
  }
  .brand-text { display: flex; flex-direction: column; }
  .brand-name {
    color: var(--gold);
    font-weight: 300;
    font-size: 19px;
    letter-spacing: 4px;
    text-transform: uppercase;
  }
  .brand-tagline {
    color: var(--gold);
    font-weight: 500;
    font-size: 6.5px;
    letter-spacing: 2px;
    margin-top: 3px;
  }
  .person { position: absolute; left: 34px; top: 112px; }
  .person-name { color: var(--gold); font-weight: 500; font-size: 18px; }
  .person-role { color: var(--ink-soft); font-size: 11px; margin-top: 1px; }
  .phones {
    position: absolute; left: 34px; top: 160px;
    list-style: none; font-size: 10.5px; color: var(--ink);
  }
  .phones li { display: flex; align-items: center; gap: 6px; line-height: 14px; }
  .phones svg { width: 9px; height: 9px; fill: var(--gold); }
  .rule {
    position: absolute; left: 34px; right: 40px;
    height: 1px; background: var(--rule);
  }
  .rule-top { top: 212px; }
  .rule-bottom { top: 276px; }
  .website-front {
    position: absolute; right: 40px; top: 194px;
    color: var(--gold); font-size: 11px; letter-spacing: 2.4px;
  }
  .address {
    position: absolute; right: 40px; top: 220px;
    text-align: right; font-size: 11px; line-height: 15px; color: var(--ink);
    font-style: normal;
  }
  /* Back */
  .card-back {
    left: 620px;
    background: radial-gradient(ellipse 62% 70% at 52% 48%, var(--gold-light) 0%, #ecd08e 45%, var(--gold-deep) 100%);
  }
  .back-brand {
    position: absolute; left: 0; right: 0; top: 100px;
    display: flex; justify-content: center; align-items: center; gap: 14px;
  }
  .back-mark {
    width: 46px; height: 46px;
    border: 4px solid var(--emboss);
    border-radius: 50%;
  }
  .back-name {
    color: var(--emboss); font-weight: 400; font-size: 26px;
    letter-spacing: 5px; text-transform: uppercase;
  }
  .website-back {
    position: absolute; left: 0; right: 0; top: 196px;
    text-align: center; color: var(--emboss);
    font-size: 13px; letter-spacing: 4px;
  }
</style>
</head>
<body>
  <section class="card card-front">
    <div class="brand">
      <span class="brand-mark"></span>
      <div class="brand-text">
        <span class="brand-name">Clearline Studio</span>
        <span class="brand-tagline">Architecture Corporate Commercial</span>
      </div>
    </div>

    <div class="person">
      <p class="person-name">Daniel Reeve</p>
      <p class="person-role">President</p>
    </div>

    <ul class="phones">
      <li><svg viewBox="0 0 10 10"><path d="M2 0.5 L3.8 2.6 L2.9 3.6 Q4 6 6.4 7.1 L7.4 6.2 L9.5 8 L8.3 9.5 Q3.5 9 0.5 1.7 Z"/></svg>555-214-7730</li>
      <li><svg viewBox="0 0 10 10"><rect x="2.5" y="0.5" width="5" height="9" rx="1"/></svg>555-618-2941</li>
      <li><svg viewBox="0 0 10 10"><rect x="0.5" y="3" width="9" height="5" rx="1"/><rect x="2.5" y="1" width="5" height="2"/></svg>555-390-4462</li>
    </ul>

    <div class="rule rule-top"></div>
    <p class="website-front">www.clearlinestudio.com</p>

    <address class="address">
      1420 Harbor View Road<br>
      Seattle, Washington 98101<br>
      hello@clearlinestudio.com
    </address>
    <div class="rule rule-bottom"></div>
  </section>

  <section class="card card-back">
    <div class="back-brand">
      <span class="back-mark"></span>
      <span class="back-name">Clearline Studio</span>
    </div>
    <p class="website-back">www.clearlinestudio.com</p>
  </section>
</body>
</html>
```